Maple Grove Schools | brand new stationery!

We need stationery design with our new logo! Our company updated it's name and image and we like to incorporate the new one on our stationery, business cards and email signature. We are looking for fresh, new ideas!
Industry: Childcare, Elementary and Middle School
Company Name: Maple Grove Schools
Tagline: Bright Futures Start Here
Main colors: Blue, white and a little yellow
Star shape is something new for us! Do you see a way to incorporate it as a design element?

```html
<!DOCTYPE html>
<html lang="en">
<head>
<meta charset="utf-8">
<title>Maple Grove Schools — Business Card</title>
<link rel="stylesheet" href="https://fonts.googleapis.com/css2?family=Montserrat:wght@400;500;600;700&display=swap">
<style>
  :root {
    --navy: #1f2470;
    --navy-deep: #181c5c;
    --navy-soft: #2c3282;
    --gold: #f9c80e;
    --ink: #1c1c22;
    --text: #4a4a52;
    --paper: #ffffff;
    --backdrop: #d9d9d6;
  }
  * { margin: 0; padding: 0; box-sizing: border-box; }
  html, body { width: 1200px; height: 801px; overflow: hidden; }
  body {
    background: var(--backdrop);
    font-family: "Montserrat", sans-serif;
    position: relative;
  }
  .card {
    position: absolute;
    top: 246px;
    width: 540px;
    height: 309px;
    overflow: hidden;
    box-shadow: 0 6px 18px rgba(0,0,0,.18);
  }
  .card--front { left: 40px; background: var(--paper); }
  .card--back  { left: 620px; background: var(--navy); }

  /* front: brand block */
  .brand {
    position: absolute;
    left: 34px; top: 92px;
    display: flex; align-items: center; gap: 14px;
  }
  .brand__dot {
    width: 40px; height: 40px; border-radius: 50%;
    background: var(--navy);
    flex: none;
  }
  .brand__name {
    font-weight: 700;
    font-size: 27px;
    line-height: 1.05;
    color: var(--ink);
  }
  .divider {
    position: absolute;
    left: 268px; top: 42px;
    width: 1px; height: 170px;
    background: var(--gold);
  }

  /* front: contact block */
  .contact {
    position: absolute;
    left: 288px; top: 40px;
    width: 240px;
  }
  .contact__name {
    font-weight: 700; font-size: 15px;
    color: var(--ink); letter-spacing: .2px;
  }
  .contact__role {
    font-weight: 500; font-size: 13px;
    color: var(--gold); margin-top: 2px;
  }
  .contact__address {
    margin-top: 16px;
    font-size: 11px; line-height: 1.45;
    color: var(--text);
  }
  .contact__list { list-style: none; margin-top: 6px; }
  .contact__item {
    display: flex; align-items: center; gap: 7px;
    font-size: 11px; line-height: 1.6; color: var(--text);
  }
  .contact__icon { width: 12px; height: 12px; flex: none; }

  /* front: bottom band */
  .band {
    position: absolute;
    left: 0; top: 262px;
    width: 400px; height: 22px;
    background: var(--navy);
    display: flex; align-items: center;
    padding-left: 180px;
  }
  .band__tagline {
    color: var(--paper);
    font-size: 10px; font-weight: 500;
    letter-spacing: 1.2px;
  }
  .band__brand {
    position: absolute;
    left: 404px; top: 262px;
    width: 76px; height: 22px;
    display: flex; align-items: center; justify-content: center;
    font-size: 7px; font-weight: 700;
    color: var(--navy);
  }
  .band__accent {
    position: absolute;
    left: 480px; top: 262px;
    width: 60px; height: 22px;
    background: var(--gold);
  }

  /* back */
  .pattern {
    position: absolute; inset: 0;
    background: linear-gradient(135deg, var(--navy-soft), var(--navy) 55%, var(--navy-deep));
  }
  .back__brand {
    position: absolute;
    right: 42px; bottom: 78px;
    font-weight: 700; font-size: 14px;
    color: var(--paper);
  }
</style>
</head>
<body>
  <section class="card card--front" aria-label="Business card front">
    <div class="brand">
      <span class="brand__dot"></span>
      <p class="brand__name">Maple Grove<br>Schools</p>
    </div>

    <span class="divider"></span>

    <div class="contact">
      <p class="contact__name">DANIEL R. WHITCOMBE</p>
      <p class="contact__role">Founder &amp; CEO</p>
      <p class="contact__address">48 Orchard Lane, Suite 4<br>Fairview, OR 97024</p>
      <ul class="contact__list">
        <li class="contact__item">
          <svg class="contact__icon" viewBox="0 0 24 24"><path fill="#1f2470" d="M6.6 10.8a15 15 0 0 0 6.6 6.6l2.2-2.2a1 1 0 0 1 1-.25 11.4 11.4 0 0 0 3.6.57 1 1 0 0 1 1 1V20a1 1 0 0 1-1 1A17 17 0 0 1 3 4a1 1 0 0 1 1-1h3.5a1 1 0 0 1 1 1c0 1.25.2 2.45.57 3.57a1 1 0 0 1-.25 1z"/></svg>
          (503) 555-0148
        </li>
        <li class="contact__item">
          <svg class="contact__icon" viewBox="0 0 24 24"><rect x="2" y="5" width="20" height="14" rx="1" fill="none" stroke="#1f2470" stroke-width="2"/><path d="M2 6l10 7 10-7" fill="none" stroke="#1f2470" stroke-width="2"/></svg>
          hello@maplegroveschools.org
        </li>
        <li class="contact__item">
          <svg class="contact__icon" viewBox="0 0 24 24"><g fill="none" stroke="#1f2470" stroke-width="1.8"><circle cx="12" cy="12" r="10"/><ellipse cx="12" cy="12" rx="4.5" ry="10"/><path d="M2 12h20M4 7h16M4 17h16"/></g></svg>
          www.maplegroveschools.org
        </li>
      </ul>
    </div>

    <div class="band"><span class="band__tagline">Bright Futures Start Here</span></div>
    <span class="band__brand">Maple Grove Schools</span>
    <span class="band__accent"></span>
  </section>

  <section class="card card--back" aria-label="Business card back">
    <div class="pattern" role="img" aria-label="Repeating embossed brand pattern in soft navy tones"></div>
    <p class="back__brand">Maple Grove Schools</p>
  </section>
</body>
</html>
```